Chimney Service company needs new business card design

We need a updated business card with our new logo added. We provide a full range of chimney services throughout Vermont and New Hampshire. The business card will be one sided and color. Attached is our current business card another document showing all the information we would like on the card.
We dont like a lot of flashy colors.... here is a link to our website to get an idea of our branding www.flueguardianvt.example

Target Market(s)

homeowners

Industry/Entity Type

Business

Contact Information for Business Card

See attached sheet for content.

Font styles to use
Serif
Sans Serif

Requirements
Must have
• all information provided on separate sheet
Should not have
• Additional information that may clogg up design

```html
<!DOCTYPE html>
<html lang="en">
<head>
<meta charset="utf-8">
<title>Flue Guardian – Business Card</title>
<link href="https://fonts.googleapis.com/css2?family=Open+Sans:wght@400;600;700&family=Cinzel:wght@400&display=swap" rel="stylesheet">
<style>
  :root {
    --backdrop: #3b3b3c;
    --card-black: #1a1a1b;
    --card-charcoal: #252627;
    --flame-red: #d9241c;
    --tab-grey: #41454a;
    --text-white: #f2f2f2;
    --emboss: #0b0b0c;
    --emboss-edge: #3a3a3c;
  }
  * { box-sizing: border-box; margin: 0; padding: 0; }
  html, body { width: 799px; height: 1200px; overflow: hidden; }
  body {
    background: var(--backdrop);
    font-family: "Open Sans", Arial, sans-serif;
    position: relative;
  }
  .card {
    position: absolute;
    left: 80px;
    width: 640px;
    height: 366px;
    border-radius: 4px;
    box-shadow: 0 14px 30px rgba(0,0,0,.45);
    overflow: hidden;
  }
  /* Front */
  .card-front { top: 150px; background: var(--card-black); }
  .brand {
    position: absolute;
    left: 0; right: 0; top: 108px;
    display: flex; flex-direction: column; align-items: center;
  }
  .brand-row { display: flex; align-items: center; gap: 16px; }
  .brand-square {
    width: 34px; height: 34px;
    background: var(--emboss);
    border: 1px solid var(--emboss-edge);
  }
  .brand-name {
    font-weight: 600;
    font-size: 40px;
    letter-spacing: 2px;
    color: var(--emboss);
    text-shadow: 0 1px 0 var(--emboss-edge);
  }
  .brand-rule {
    width: 360px; height: 1px; margin-top: 10px;
    background: var(--emboss-edge);
  }
  .brand-since {
    margin-top: 8px;
    font-family: "Cinzel", Georgia, serif;
    font-size: 16px; letter-spacing: 3px;
    color: var(--emboss);
    text-shadow: 0 1px 0 var(--emboss-edge);
  }
  /* Back */
  .card-back { top: 680px; background: var(--card-charcoal); color: var(--text-white); }
  .services { position: absolute; left: 30px; top: 26px; list-style: none; }
  .services li {
    font-size: 16px; line-height: 24px;
    display: flex; align-items: center; gap: 10px;
  }
  .services li::before {
    content: ""; width: 8px; height: 8px;
    background: var(--flame-red); border-radius: 50%;
  }
  .coverage { position: absolute; left: 30px; top: 158px; width: 300px; }
  .coverage-title {
    color: var(--flame-red); font-weight: 700; font-size: 18px;
    line-height: 24px; white-space: nowrap;
  }
  .coverage-since {
    display: flex; align-items: center; gap: 8px;
    font-size: 10px; line-height: 14px; letter-spacing: 1px; margin-top: 2px;
  }
  .coverage-since::before, .coverage-since::after {
    content: ""; flex: 1; height: 2px; background: var(--flame-red);
  }
  .contact { position: absolute; left: 30px; top: 210px; list-style: none; }
  .contact li {
    display: flex; align-items: center; gap: 12px;
    font-size: 14px; line-height: 22px; white-space: nowrap;
  }
  .contact svg { width: 13px; height: 13px; fill: var(--flame-red); flex: none; }
  .contact .accent { color: var(--flame-red); }
  .flame-area {
    position: absolute; left: 450px; top: 90px;
    width: 150px; height: 210px;
    background: linear-gradient(180deg, #e0302a, #b81c16);
    border-radius: 70px 70px 20px 20px;
  }
  .band-insured {
    position: absolute; left: 0; bottom: 30px;
    width: 360px; height: 34px;
    background: var(--flame-red);
    border-radius: 0 6px 6px 0;
    font-size: 13px; line-height: 34px; padding-left: 30px;
  }
  .tab-family {
    position: absolute; right: 0; bottom: 0;
    width: 270px; height: 58px;
    background: var(--tab-grey);
    border-radius: 8px 0 0 0;
    font-size: 14px; text-align: center; line-height: 58px;
  }
</style>
</head>
<body>
  <section class="card card-front">
    <div class="brand">
      <div class="brand-row">
        <span class="brand-square"></span>
        <span class="brand-name">FLUE GUARDIAN</span>
      </div>
      <div class="brand-rule"></div>
      <div class="brand-since">INC 1989</div>
    </div>
  </section>

  <section class="card card-back">
    <ul class="services">
      <li>Full Masonry Services</li>
      <li>Historic chimney restoration</li>
      <li>Stainless steel liners</li>
      <li>New Chimney installations</li>
      <li>Guild Certified Chimney sweeps</li>
    </ul>
    <div class="coverage">
      <div class="coverage-title">Serving VT and New Hampshire</div>
      <div class="coverage-since">SINCE 1989</div>
    </div>
    <ul class="contact">
      <li><svg viewBox="0 0 16 16"><path d="M3 1h3l1.5 4-2 1.2a9 9 0 0 0 4.3 4.3L11 8.5l4 1.5v3a2 2 0 0 1-2 2A12 12 0 0 1 1 3a2 2 0 0 1 2-2z"/></svg><span>802-555-0148</span></li>
      <li><svg viewBox="0 0 16 16"><path d="M1 3h14v10H1z"/></svg><span>info@flueguardianvt.example</span></li>
      <li><svg viewBox="0 0 16 16"><circle cx="8" cy="8" r="7"/></svg><span>www.<span class="accent">flueguardianvt</span>.example</span></li>
    </ul>
    <div class="flame-area" role="img" aria-label="Large red flame decoration"></div>
    <div class="band-insured">Fully Insured – Free Estimates</div>
    <div class="tab-family">Family Owned &amp; Operated</div>
  </section>
</body>
</html>
```